Navoro & Omvar Automotive Repair Shop. Need a new website design.

We specialize in Navoro & Omvar auto repair, but also work on other Asian import vehicles. We have been in business for 7 years and pride ourselves on high quality auto repair that is fixed right the first time. Would like the automotive repair website to incorporate the colors black, red and white if possible and have our logo and some Navoro and Omvar vehicles included in the website.

Target Market(s)

Navoro & Omvar vehicle owners

Industry/Entity Type

Automotive Repair

Coding

Coded - Design and coding required

Number of Pages Required

5+ page

Colors
EB3D1F
EC4F4E
F09395
F8D3D4
FCEDEE

Requirements
Must have
• Home, Services, Contact Us, Schedule appointment, and a gallery tab that I can add shop pictures to when completed.
Nice to have
• Would like to see example pictures of job next to each service listed.
Should not have
• Service not related to auto repair. Ex. auto detailing, towing, car wash

```html
<!DOCTYPE html>
<html lang="en">
<head>
<meta charset="utf-8">
<title>Korvel Automotive – Testimonials</title>
<link href="https://fonts.googleapis.com/css2?family=Fira+Sans+Extra+Condensed:wght@400;600;700&family=Open+Sans:ital,wght@0,400;0,600;0,700;1,400;1,700&display=swap" rel="stylesheet">
<style>
:root{
  --red:#eb1c0f;
  --star:#f05a1e;
  --star-soft:#f09395;
  --black:#000;
  --ink:#111;
  --body:#333;
  --footer:#1c1c1c;
  --white:#fff;
}
*{margin:0;padding:0;box-sizing:border-box}
html,body{width:722px;height:1200px;overflow:hidden;background:var(--white)}
body{position:relative;font-family:"Open Sans",sans-serif;color:var(--body)}

/* header */
.site-header{position:absolute;left:0;top:0;width:722px;height:73px;background:var(--black)}
.site-header .rule{position:absolute;left:0;top:71px;width:212px;height:2px;background:var(--red)}
.site-header .slash{position:absolute;left:0;top:0}
.brand{position:absolute;left:75px;top:20px;display:flex;align-items:center;gap:5px}
.brand .mark{width:10px;height:10px;background:var(--red)}
.brand .name{font-family:"Fira Sans Extra Condensed",sans-serif;font-weight:700;font-size:19px;color:var(--white);letter-spacing:.5px}
.info{position:absolute;top:12px;display:flex;align-items:center;gap:5px;color:var(--white);font-style:italic;font-size:8px;line-height:10px}
.info .icon{width:22px;height:22px;border-radius:50%;background:#3a3a3a;border:1px solid #777;display:flex;align-items:center;justify-content:center}
.info .accent{color:var(--red);font-weight:700}
.info .stars-top{color:var(--red);font-size:10px;font-style:normal}
.nav{position:absolute;top:56px;left:0;width:722px;font-size:7px;font-weight:700;color:var(--white)}
.nav a{position:absolute;color:inherit;text-decoration:none}
.nav a.active{color:var(--red)}

/* hero */
.hero{position:absolute;left:0;top:73px;width:722px;height:190px;overflow:hidden}
.hero .photo{position:absolute;inset:0;background:linear-gradient(90deg,#1a1a1a 0%,#2a2a2a 35%,#6d6a68 55%,#a8a4a0 75%,#c9c7c4 100%)}
.hero .overlay{position:absolute;left:0;top:0}
.hero .eyebrow{position:absolute;left:68px;top:64px;display:flex;align-items:center;gap:6px;color:var(--white);font-size:6px;font-weight:600;letter-spacing:.4px}
.hero .eyebrow i{display:block;width:24px;height:1px;background:var(--white)}
.hero h1{position:absolute;left:66px;top:75px;font-family:"Fira Sans Extra Condensed",sans-serif;font-weight:700;font-size:31px;color:var(--white);line-height:36px}
.hero p{position:absolute;left:67px;top:113px;width:200px;font-size:7px;line-height:10px;color:var(--white)}
.hero-band{position:absolute;left:0;top:262px}

/* reviews */
.intro{position:absolute;left:0;top:325px;width:722px;text-align:center}
.intro h2{font-family:"Fira Sans Extra Condensed",sans-serif;font-weight:600;font-size:22px;color:var(--ink);line-height:26px}
.intro p{width:260px;margin:7px auto 0;font-size:7px;line-height:12px}
.review-col{position:absolute;width:141px;display:flex;flex-direction:column;gap:8px}
.review{position:relative;width:141px;background:var(--white);box-shadow:0 6px 14px rgba(0,0,0,.09);padding:15px 14px 14px 17.5px}
.review .avatar{width:41px;height:41px;border-radius:50%;background:radial-gradient(circle at 50% 40%,#b9a89c 0%,#6e625c 55%,#2d2a2a 100%)}
.review .quote{position:absolute;left:32px;top:48px;font-family:Georgia,serif;font-weight:700;font-size:17px;line-height:17px;color:var(--red)}
.review .name{position:absolute;left:68px;top:20px;font-family:"Fira Sans Extra Condensed",sans-serif;font-weight:400;font-size:10.5px;line-height:13px;color:var(--ink)}
.review .stars{position:absolute;left:68px;top:34px;font-size:7px;line-height:9px;color:var(--star);letter-spacing:1px}
.review .stars.soft{color:var(--star-soft)}
.review p{margin-top:8px;font-size:6.8px;line-height:10.2px;color:var(--body)}
.review.featured{background:var(--red);clip-path:polygon(25px 0,100% 0,100% 100%,0 100%,0 34px);box-shadow:none;padding-top:15px;padding-bottom:22px}
.review.featured .name,.review.featured .stars,.review.featured .quote{color:var(--white)}
.review.featured p{color:var(--white);font-weight:600}

.load-more{position:absolute;left:313px;top:886px;width:96px;height:26px;background:var(--red);clip-path:polygon(14px 0,100% 0,100% 100%,0 100%,0 14px);color:var(--white);font-family:"Fira Sans Extra Condensed",sans-serif;font-weight:600;font-size:8px;letter-spacing:.3px;display:flex;align-items:center;justify-content:center;gap:3px}
.load-more b{font-size:11px;font-weight:700}

/* footer */
.site-footer{position:absolute;left:0;top:959px;width:722px;height:241px;background:var(--footer);color:var(--white)}
.f-brand{position:absolute;left:68px;top:45px;display:flex;align-items:center;gap:6px}
.f-brand .mark{width:14px;height:14px;background:var(--red)}
.f-brand .name{font-family:"Fira Sans Extra Condensed",sans-serif;font-weight:700;font-size:24px;color:var(--white);line-height:27px}
.badge{position:absolute;background:var(--white)}
.f-title{position:absolute;top:33px;font-family:"Fira Sans Extra Condensed",sans-serif;font-weight:600;font-size:12px;color:var(--red)}
.links{position:absolute;left:221px;top:61px;list-style:none;font-size:7px}
.links li{height:19.3px}
.contact-row{position:absolute;left:305px;display:flex;align-items:center;gap:8px;font-size:7px;line-height:10px}
.contact-row .ic{width:18px;height:18px;border-radius:50%;background:#555;border:1px solid #888;display:flex;align-items:center;justify-content:center;flex:none}
.contact-row em{font-style:normal;color:var(--red)}
.map{position:absolute;left:478px;top:38px;width:176px;height:126px;background:linear-gradient(135deg,#e9ece9 0%,#dfe6e0 50%,#e7e3d6 100%);clip-path:polygon(14px 0,100% 0,100% 100%,0 100%,0 14px);border:2px solid var(--white)}
.social{position:absolute;top:213px;width:17px;height:17px;border-radius:50%;background:#666;border:1px solid #999}
.copyright{position:absolute;left:460px;top:223px;font-size:7px;font-weight:600;color:var(--white)}
</style>
</head>
<body>

<header class="site-header">
  <svg class="slash" width="722" height="73" aria-hidden="true">
    <polygon points="205,73 218,48 223,48 210,73" fill="var(--red)"/>
    <polygon points="212,73 222,52 224,52 214,73" fill="#fff" opacity=".8"/>
  </svg>
  <div class="rule"></div>
  <div class="brand"><span class="mark"></span><span class="name">KORVEL AUTOMOTIVE</span></div>

  <div class="info" style="left:312px">
    <span class="icon"><svg width="10" height="10" viewBox="0 0 10 10"><circle cx="5" cy="4" r="3" fill="none" stroke="#fff" stroke-width="1"/><path d="M3 7 L3 10 L5 9 L7 10 L7 7" fill="none" stroke="#fff" stroke-width=".8"/></svg></span>
    <span><span class="stars-top">★★★★★</span><br>5 Star Service</span>
  </div>
  <div class="info" style="left:430px">
    <span class="icon"><svg width="10" height="10" viewBox="0 0 10 10"><path d="M1 1 L9 9 M9 1 L1 9" stroke="#fff" stroke-width="1.3"/></svg></span>
    <span>Quality Service<br><span class="accent">Guarantee</span></span>
  </div>
  <div class="info" style="left:554px">
    <span class="icon"><svg width="10" height="10" viewBox="0 0 10 10"><path d="M2 1 L4 1 L5 3 L4 4 Q5 6 6 6 L7 5 L9 6 L9 8 Q7 10 4 7 Q0 3 2 1Z" fill="#fff"/></svg></span>
    <span>Call Us For Booking<br><span class="accent">555.013.4821</span></span>
  </div>

  <nav class="nav">
    <a style="left:350px">HOME</a>
    <a style="left:390px">ABOUT US</a>
    <a style="left:444px">SERVICES ˅</a>
    <a style="left:494px">GALLERY</a>
    <a class="active" style="left:543px">TESTIMONIALS</a>
    <a style="left:611px">CONTACT US</a>
  </nav>
</header>

<section class="hero">
  <div class="photo" role="img" aria-label="Smiling mechanic and customer reviewing a clipboard in the repair shop"></div>
  <svg class="overlay" width="722" height="190" aria-hidden="true">
    <defs>
      <linearGradient id="fade" x1="0" x2="1"><stop offset="0" stop-color="#000" stop-opacity=".85"/><stop offset="1" stop-color="#000" stop-opacity="0"/></linearGradient>
    </defs>
    <rect width="320" height="190" fill="url(#fade)"/>
    <polygon points="160,0 360,0 272,190 68,190" fill="#c0000a" opacity=".55"/>
  </svg>
  <div class="eyebrow"><i></i>TESTIMONIALS</div>
  <h1>What Our Clients Say</h1>
  <p>Quisque lorem neque, ultricies eget risus quis, fringilla interdum augue. Donec sollicitudin in ante sed consequat.</p>
</section>
<svg class="hero-band" width="722" height="26" aria-hidden="true">
  <polygon points="198,0 722,0 722,19 647,19 564,2 226,23" fill="var(--red)"/>
</svg>

<section class="intro">
  <h2>See Some Of The Reviews Here</h2>
  <p>Quisque lorem neque, ultricies eget risus quis, fringilla interdum augue. Donec sollicitudin in ante sed conbulum ut risus sit amet.</p>
</section>

<div class="review-col" style="left:67px;top:414px">
  <article class="review">
    <div class="avatar" role="img" aria-label="Customer portrait"></div><span class="quote">“</span>
    <h3 class="name">Dana Wells</h3><div class="stars">★★★★★</div>
    <p>Lorem ipsum dolor sit amet, consectetur adipiscing elit. Ut non ipsum eleifend turpis vulputate pulvinar sit amet quis nulla. Vest ibulum luctus nibh ligula, nec con dimentum velit facilisis a. Nam cursus eu turpis a lacinia.</p>
  </article>
  <article class="review" style="padding-bottom:20px">
    <div class="avatar" role="img" aria-label="Customer portrait"></div><span class="quote">“</span>
    <h3 class="name">Dana Wells</h3><div class="stars">★★★★★</div>
    <p>I would highly recommend Korvel Automotive to family, friends, &amp; co-workers! I'm a repeat customer myself!</p>
  </article>
  <article class="review" style="padding-bottom:20px">
    <div class="avatar" role="img" aria-label="Customer portrait"></div><span class="quote">“</span>
    <h3 class="name">Dana Wells</h3><div class="stars">★★★★★</div>
    <p>I would highly recommend Korvel Automotive to family, friends, &amp; co-workers! I'm a repeat customer myself!</p>
  </article>
</div>

<div class="review-col" style="left:216px;top:407px">
  <article class="review featured">
    <div class="avatar" role="img" aria-label="Customer portrait"></div><span class="quote">“</span>
    <h3 class="name">Dana Wells</h3><div class="stars">★★★★★</div>
    <p>I would highly recommend Korvel Automotive to family, friends, &amp; co-workers! I'm a repeat customer myself!</p>
  </article>
  <article class="review">
    <div class="avatar" role="img" aria-label="Customer portrait"></div><span class="quote">“</span>
    <h3 class="name">Dana Wells</h3><div class="stars soft">★★★★★</div>
    <p>Lorem ipsum dolor sit amet, consectetur adipiscing elit. Ut non ipsum eleifend turpis vulputate pulvinar sit amet quis nulla. Vest ibulum luctus nibh ligula, nec con dimentum velit facilisis a. Nam cursus eu turpis a lacinia. Lorem ipsum dolor sit amet, consectetur adipiscinnon ipsum.</p>
  </article>
  <article class="review" style="padding-bottom:18px">
    <div class="avatar" role="img" aria-label="Customer portrait"></div><span class="quote">“</span>
    <h3 class="name">Dana Wells</h3><div class="stars soft">★★★★★</div>
    <p>Lorem ipsum dolor sit amet, consectetur adipiscing elit. Ut non ipsum eleifend turpis vulputate pulvinar sit amet quis nulla.</p>
  </article>
</div>

<div class="review-col" style="left:364px;top:414px">
  <article class="review">
    <div class="avatar" role="img" aria-label="Customer portrait"></div><span class="quote">“</span>
    <h3 class="name">Dana Wells</h3><div class="stars">★★★★★</div>
    <p>Lorem ipsum dolor sit amet, consectetur adipiscing elit. Ut non ipsum eleifend turpis vulputate pu lvinar sit amet quis nulla. Vestibulum luctus nibh ligula, nec condimentum velit facilisis a. Nam cursus eu turpis a lacinia. Ut efficitur tortor hendrerit dui condimentum, quis volutpat nisl dapibus. Pellentesque.</p>
  </article>
  <article class="review" style="padding-bottom:20px">
    <div class="avatar" role="img" aria-label="Customer portrait"></div><span class="quote">“</span>
    <h3 class="name">Dana Wells</h3><div class="stars">★★★★★</div>
    <p>I would highly recommend Korvel Automotive to family, friends, &amp; co-workers! I'm a repeat customer myself!</p>
  </article>
  <article class="review" style="padding-bottom:20px">
    <div class="avatar" role="img" aria-label="Customer portrait"></div><span class="quote">“</span>
    <h3 class="name">Dana Wells</h3><div class="stars">★★★★★</div>
    <p>I would highly recommend Korvel Automotive to family, friends, &amp; co-workers! I'm a repeat customer myself!</p>
  </article>
</div>

<div class="review-col" style="left:513px;top:414px">
  <article class="review" style="padding-bottom:18px">
    <div class="avatar" role="img" aria-label="Customer portrait"></div><span class="quote">“</span>
    <h3 class="name">Dana Wells</h3><div class="stars">★★★★★</div>
    <p>Sed non varius augue. Fusce a felis in dui faucibus porttitor. Duis mollis eget orci non eleifend. Sed eu turpis laoreet, dignissim nibh ut, posuere enim.</p>
  </article>
  <article class="review" style="padding-bottom:20px">
    <div class="avatar" role="img" aria-label="Customer portrait"></div><span class="quote">“</span>
    <h3 class="name">Dana Wells</h3><div class="stars">★★★★★</div>
    <p>I would highly recommend Korvel Automotive to family, friends, &amp; co-workers! I'm a repeat customer myself!</p>
  </article>
  <article class="review">
    <div class="avatar" role="img" aria-label="Customer portrait"></div><span class="quote">“</span>
    <h3 class="name">Dana Wells</h3><div class="stars">★★★★★</div>
    <p>Lorem ipsum dolor sit amet, consectetur adipiscing elit. Ut non ipsum eleifend turpis vulputate pulvinar sit amet quis nulla. Vest ibulum luctus nibh ligula, nec con dimentum velit facilisis a.</p>
  </article>
</div>

<a class="load-more"><b>+</b> LOAD MORE</a>

<footer class="site-footer">
  <div class="f-brand"><span class="mark"></span><span class="name">KORVEL<br>AUTOMOTIVE</span></div>
  <div class="badge" style="left:68px;top:139px;width:55px;height:22px" aria-label="Partner badge"></div>
  <div class="badge" style="left:126px;top:139px;width:45px;height:22px" aria-label="Partner badge"></div>
  <div class="badge" style="left:68px;top:165px;width:30px;height:21px" aria-label="Certification badge"></div>
  <div class="badge" style="left:100px;top:165px;width:55px;height:21px" aria-label="Financing partner badge"></div>

  <h4 class="f-title" style="left:221px">Quick Links.</h4>
  <ul class="links">
    <li>Home</li><li>About Us</li><li>Services</li><li>Gallery</li><li>Testimonials</li><li>Contact Us</li>
  </ul>

  <h4 class="f-title" style="left:310px">Contact Us</h4>
  <div class="contact-row" style="top:62px">
    <span class="ic"><svg width="8" height="9" viewBox="0 0 8 9"><path d="M4 9 L1 4.5 A3 3 0 1 1 7 4.5Z" fill="#fff"/><circle cx="4" cy="3.3" r="1.1" fill="#555"/></svg></span>
    <span>418 Harbor Crest Way #5<br>Dalemont, TX 75099</span>
  </div>
  <div class="contact-row" style="top:91px">
    <span class="ic"><svg width="8" height="8" viewBox="0 0 10 10"><path d="M2 1 L4 1 L5 3 L4 4 Q5 6 6 6 L7 5 L9 6 L9 8 Q7 10 4 7 Q0 3 2 1Z" fill="#fff"/></svg></span>
    <span><em>OFFICE:</em> 555.013.4821<br><em>Phone:</em> 555.018.2260</span>
  </div>
  <div class="contact-row" style="top:122px">
    <span class="ic"><svg width="8" height="6" viewBox="0 0 8 6"><rect width="8" height="6" fill="#fff"/><path d="M0 0 L4 3.5 L8 0" fill="none" stroke="#555" stroke-width=".8"/></svg></span>
    <span>KorvelAutomotive@inbox.net</span>
  </div>
  <div class="contact-row" style="top:149px">
    <span class="ic"><svg width="9" height="9" viewBox="0 0 10 10"><circle cx="5" cy="5" r="4.5" fill="#fff"/><path d="M5 2 L5 5 L7 6.5" stroke="#555" stroke-width="1" fill="none"/></svg></span>
    <span><em>Hours of Operation:</em> M-F 8:30-6pm</span>
  </div>

  <div class="map" role="img" aria-label="Street map showing the shop location"></div>

  <svg style="position:absolute;left:0;top:0" width="722" height="241" aria-hidden="true">
    <polygon points="208,216 722,216 722,241 194,241" fill="var(--red)"/>
    <polygon points="196,241 203,241 215,216 208,216" fill="#fff" opacity=".85"/>
    <polygon points="186,241 192,241 204,216 198,216" fill="var(--red)"/>
    <rect x="0" y="239" width="190" height="2" fill="var(--red)"/>
  </svg>
  <span class="social" style="left:91px" aria-label="Social profile"></span>
  <span class="social" style="left:112px" aria-label="Social profile"></span>
  <span class="social" style="left:132px" aria-label="Social profile"></span>
  <p class="copyright">Copyright © 2024 Korvel Automotive LLC. All Rights Reserved.</p>
</footer>

</body>
</html>
```